Flight school sign for building, banner, and bilboard

This sign is primarily for use on the side of our flight school building to draw attention for current and future flight school students. We offer airplane and helicopter flight training, ground school training and seminars, airplane and helicopter rentals, multi-engine training, and more. I would like a professional but exciting sign that can be used across a multitude of signage options such as banners, banner ads, billboard, and other mediums so that our sign is consistent and recognizable.

Contact Information for Business Card

The business card should match our company sign somewhat but not exactly. We want good and exciting imagery or wording and energizing/exciting colors.

```html
<!DOCTYPE html>
<html lang="en">
<head>
<meta charset="utf-8">
<title>Skyward Aviation – Flight School Banner</title>
<link rel="stylesheet" href="https://fonts.googleapis.com/css2?family=Oswald:wght@600;700&family=Open+Sans:wght@600;700&family=Rubik:wght@500;600&display=swap">
<style>
  :root {
    --navy: #1f2d5c;
    --navy-deep: #17224a;
    --red: #e3151a;
    --red-dark: #b80f13;
    --white: #ffffff;
    --paper: #f3f4f6;
    --stage: #d6d6d8;
  }
  * { margin: 0; padding: 0; box-sizing: border-box; }
  html, body { width: 1067px; height: 1200px; overflow: hidden; background: var(--stage); }
  .stage { position: relative; width: 1067px; height: 1200px; }
  .banner {
    position: absolute; left: 56px; top: 449px;
    width: 1074px; height: 340px;
    transform: scale(0.889); transform-origin: 0 0;
    box-shadow: 0 12px 22px rgba(0,0,0,.35);
    overflow: hidden; background: var(--paper);
  }
  .banner-shapes { position: absolute; inset: 0; }
  .brand {
    position: absolute; left: 150px; top: 58px; width: 230px;
    text-align: center; color: var(--navy);
  }
  .brand-mark { display: block; width: 36px; height: 36px; margin: 0 auto 8px; border-radius: 50%; background: var(--navy); }
  .brand-name { font: 600 20px/1 "Rubik", sans-serif; letter-spacing: .5px; }
  .brand-tagline { font: 700 6.5px/1 "Open Sans", sans-serif; color: var(--red); margin-top: 4px; letter-spacing: .3px; }
  .headline {
    position: absolute; left: 0; top: 136px; width: 560px; text-align: center;
    font-family: "Oswald", sans-serif; font-weight: 700; line-height: .95; text-transform: uppercase;
  }
  .headline-top { display: block; color: var(--navy); font-size: 56px; letter-spacing: .5px; }
  .headline-bottom { display: block; color: var(--red); font-size: 54px; letter-spacing: .5px; }
  .phone {
    position: absolute; left: 20px; top: 262px; height: 70px;
    display: flex; align-items: center; gap: 20px;
    color: var(--white); font: 600 58px/1 "Rubik", sans-serif;
  }
  .phone svg { width: 46px; height: 46px; }
  .offer { position: absolute; left: 550px; top: 18px; width: 510px; text-align: center; }
  .offer-title {
    display: flex; align-items: center; justify-content: center; gap: 16px;
    color: var(--red); font: 700 50px/1 "Oswald", sans-serif; text-transform: uppercase;
  }
  .offer-title::before, .offer-title::after { content: ""; width: 96px; height: 6px; background: var(--red); }
  .offer-list { list-style: none; margin-top: 12px; }
  .offer-list li {
    color: var(--white); font: 600 25px/1 "Open Sans", sans-serif;
    padding: 11px 0 13px; position: relative;
  }
  .offer-list li + li::before {
    content: ""; position: absolute; left: 50%; top: 0; width: 190px; height: 2px;
    transform: translateX(-50%); background: linear-gradient(90deg, transparent, var(--red), transparent);
  }
  .site {
    position: absolute; left: 648px; top: 282px; width: 324px; height: 42px;
    border-radius: 21px; background: linear-gradient(180deg, var(--red), var(--red-dark));
    color: var(--white); font: 700 24px/42px "Open Sans", sans-serif; text-align: center;
  }
</style>
</head>
<body>
<main class="stage">
  <section class="banner">
    <svg class="banner-shapes" viewBox="0 0 1074 340" preserveAspectRatio="none">
      <defs>
        <linearGradient id="navyPanel" x1="0" y1="0" x2="1" y2="1">
          <stop offset="0" stop-color="#26366b"/>
          <stop offset="1" stop-color="#17224a"/>
        </linearGradient>
        <radialGradient id="silhouetteGlow" cx="0.5" cy="0.5" r="0.5">
          <stop offset="0" stop-color="#111a38" stop-opacity=".55"/>
          <stop offset="1" stop-color="#111a38" stop-opacity="0"/>
        </radialGradient>
      </defs>
      <polygon points="0,256 548,256 575,340 0,340" fill="var(--navy)"/>
      <polygon points="530,0 1074,0 1074,340 640,340" fill="url(#navyPanel)"/>
      <ellipse cx="850" cy="200" rx="200" ry="140" fill="url(#silhouetteGlow)" role="img" aria-label="faint airplane silhouette in the background"/>
      <polygon points="455,0 535,0 650,340 560,340" fill="var(--red)" role="img" aria-label="red airplane silhouette flying upward"/>
      <polygon points="1074,298 1074,340 1032,340" fill="var(--red)"/>
    </svg>

    <div class="brand">
      <span class="brand-mark"></span>
      <div class="brand-name">SKYWARD AVIATION</div>
      <div class="brand-tagline">YOUR FIRST LESSON STARTS WITH ONE CALL</div>
    </div>

    <h1 class="headline">
      <span class="headline-top">Future Flight</span>
      <span class="headline-bottom">School Students</span>
    </h1>

    <div class="phone">
      <svg viewBox="0 0 48 48" aria-hidden="true">
        <path d="M14 6l7 9-4 5c2 5 6 9 11 11l5-4 9 7-5 7C22 41 7 26 7 11z" fill="var(--red)"/>
        <path d="M29 8a14 14 0 0 1 11 11M29 14a8 8 0 0 1 5 5" stroke="var(--red)" stroke-width="3" fill="none" stroke-linecap="round"/>
      </svg>
      <span>5550- 142- 368</span>
    </div>

    <div class="offer">
      <h2 class="offer-title">We Offer</h2>
      <ul class="offer-list">
        <li>Airplane and helicopter flight training</li>
        <li>Airplane and helicopter rentals</li>
        <li>Ground school training and seminars</li>
        <li>Multi-engine training and more</li>
      </ul>
    </div>

    <div class="site">www.skywardaviation.com</div>
  </section>
</main>
</body>
</html>
```